Website for IT consulting Company

I need a website upgrade, the existing site content is ok, I would also like to add a testimonial page, the site should be something that is easy for us to update content. You use the content from www.kelvanbrook.com as an example. I will also post update logo and artwork. I also need a contact form with some type of validation or captcha.

I added Coded to the Project

Please omit Address maps

Target Market(s)

small business, service oriented companies. We provide IT Consulting, support and mangement

Industry/Entity Type

Information Technology

Coding

Number of Pages Required

1 page

Font styles to use
Serif
Sans Serif

Requirements
Must have
• Contain logo attached, and content from existing web site www.kelvanbrook.com.
• Also need to update content easily, and be movable to different platforms.
• There is a catch phrase
• "Let us worry about your technology…” “ so you don’t have to!”
• Should be included.
Nice to have
• Testimonial page, Project page where we can post new and past projects and pictures
Should not have
• none

```html
<!DOCTYPE html>
<html lang="en">
<head>
<meta charset="utf-8">
<title>Kelvanbrook – IT Solutions</title>
<link href="https://fonts.googleapis.com/css2?family=Ubuntu:wght@500;700&family=Open+Sans:wght@400;600&family=Arimo:wght@400;700&display=swap" rel="stylesheet">
<style>
  :root{
    --orange:#f47b20;
    --amber:#f7941d;
    --dark:#1a1a1a;
    --darker:#151515;
    --rule:#2a2a2a;
    --white:#ffffff;
    --panel:#f2f2f2;
    --heading:#444444;
    --body:#555555;
    --muted:#888888;
    --social:#555555;
    --brand-grey:#c9c9c9;
  }
  *{margin:0;padding:0;box-sizing:border-box}
  html,body{width:1088px;height:1200px;overflow:hidden;background:var(--white)}
  body{position:relative;font-family:"Arimo",Arial,sans-serif}

  .topbar{position:absolute;left:0;top:0;width:1088px;height:89px;background:var(--dark);border-bottom:1px solid var(--rule)}
  .topbar__headline{position:absolute;left:88px;top:22px;font-family:"Ubuntu",sans-serif;font-weight:700;font-size:23px;color:var(--amber);letter-spacing:.2px}
  .topbar__sub{position:absolute;left:88px;top:63px;font-size:11px;color:var(--white);letter-spacing:-.2px}
  .social{position:absolute;left:822px;top:30px;display:flex;gap:4px}
  .social span{width:20px;height:20px;background:var(--social);border-radius:2px}
  .search{position:absolute;left:988px;top:33px}

  .navbar{position:absolute;left:0;top:89px;width:1088px;height:97px;background:var(--darker)}
  .brand{position:absolute;left:88px;top:28px;display:flex;align-items:center;gap:10px}
  .brand__mark{width:30px;height:30px;background:var(--orange);border-radius:4px}
  .brand__name{font-family:"Open Sans",sans-serif;font-weight:600;font-size:30px;line-height:40px;color:var(--brand-grey);letter-spacing:.5px}
  .nav{position:absolute;top:36px;left:0;width:1088px;height:28px}
  .nav a{position:absolute;top:0;height:27px;line-height:27px;font-size:11.5px;color:var(--white);text-decoration:none}
  .nav a.is-active{background:var(--orange);padding:0 10px;border-radius:1px}

  .hero{position:absolute;left:0;top:186px;width:1088px;height:400px;
    background:linear-gradient(100deg,#3c4a5c 0%,#b9c6d3 18%,#e7ecf1 40%,#c9b6a6 52%,#eef1f5 68%,#d7c4b6 82%,#e4ebf2 100%)}
  .hero__shade{position:absolute;inset:0;background:linear-gradient(90deg,rgba(0,0,0,.25),rgba(0,0,0,.05) 60%,rgba(0,0,0,0))}
  .hero__title{position:absolute;left:88px;top:120px;font-family:"Open Sans",sans-serif;font-weight:600;font-size:30px;line-height:31px;color:var(--white)}
  .hero__text{position:absolute;left:88px;top:196px;font-family:"Open Sans",sans-serif;font-weight:600;font-size:13px;color:var(--white)}
  .hero__btn{position:absolute;left:88px;top:240px;width:89px;height:31px;line-height:31px;text-align:center;background:var(--orange);color:var(--white);font-size:11.5px;border-radius:2px}
  .hero__arrow{position:absolute;top:180px;width:32px;height:32px;background:var(--orange);border-radius:2px;display:flex;align-items:center;justify-content:center}
  .hero__arrow--prev{left:8px}
  .hero__arrow--next{left:1048px}
  .hero__dots{position:absolute;top:354px;left:498px;display:flex;gap:15px}
  .hero__dots span{width:17px;height:17px;border-radius:50%;border:2px solid var(--white)}
  .hero__dots span.is-active{background:var(--orange);border-color:var(--orange)}

  .services{position:absolute;left:0;top:586px;width:1088px;height:475px;background:var(--panel)}
  .section-title{position:absolute;left:0;width:1088px;text-align:center;font-family:"Open Sans",sans-serif;font-weight:400;font-size:30px;line-height:40px;color:var(--heading)}
  .section-lead{position:absolute;left:274px;width:540px;text-align:center;font-size:13px;line-height:19px;color:var(--body)}
  .service{position:absolute;width:300px;height:90px}
  .service__icon{position:absolute;left:0;top:0;width:88px;height:88px;border-radius:50%;background:var(--white);border:4px solid #e9e9e9;display:flex;align-items:center;justify-content:center}
  .service__name{position:absolute;left:108px;top:6px;font-family:"Open Sans",sans-serif;font-weight:400;font-size:13px;color:var(--heading);text-transform:uppercase}
  .service__text{position:absolute;left:108px;top:36px;font-family:"Open Sans",sans-serif;font-size:13px;line-height:19px;color:var(--muted)}

  .works{position:absolute;left:0;top:1061px;width:1088px;height:139px;background:var(--white)}
</style>
</head>
<body>

<header class="topbar">
  <div class="topbar__headline">IT SOLUTIONS THAT WORK FOR YOUR BUSINESS.</div>
  <div class="topbar__sub">A FULL SERVICE TECHNOLOGY COMPANY.</div>
  <div class="social" aria-label="Social links"><span></span><span></span><span></span><span></span><span></span></div>
  <svg class="search" width="12" height="12" viewBox="0 0 12 12" aria-label="Search"><circle cx="5" cy="5" r="3.6" fill="none" stroke="#fff" stroke-width="1.8"/><line x1="7.6" y1="7.6" x2="11" y2="11" stroke="#fff" stroke-width="2"/></svg>
</header>

<nav class="navbar">
  <div class="brand"><span class="brand__mark"></span><span class="brand__name">KELVANBROOK</span></div>
  <div class="nav">
    <a class="is-active" style="left:502px">Home</a>
    <a style="left:589px">About Us</a>
    <a style="left:682px">Support</a>
    <a style="left:769px">Clients</a>
    <a style="left:851px">Careers</a>
    <a style="left:939px">Contact</a>
  </div>
</nav>

<section class="hero" role="img" aria-label="Photo of hands reviewing printed business charts beside a tablet">
  <div class="hero__shade"></div>
  <h1 class="hero__title">Lorem ipsum dolor sit amet<br>consectetur adipisicing elit</h1>
  <p class="hero__text">Accusantium doloremque laudantium totam rem aperiam, eaque ipsa...</p>
  <div class="hero__btn">Read More</div>
  <div class="hero__arrow hero__arrow--prev"><svg width="10" height="12" viewBox="0 0 10 12"><path d="M7 1 2 6l5 5" fill="none" stroke="#fff" stroke-width="2.4"/></svg></div>
  <div class="hero__arrow hero__arrow--next"><svg width="10" height="12" viewBox="0 0 10 12"><path d="M3 1l5 5-5 5" fill="none" stroke="#fff" stroke-width="2.4"/></svg></div>
  <div class="hero__dots"><span class="is-active"></span><span></span><span></span></div>
</section>

<section class="services">
  <h2 class="section-title" style="top:52px">IT Support Solutions</h2>
  <p class="section-lead" style="top:102px">Lorem ipsum dolor sit amet, consectetur adipisicing elit, sed do eiusmod tempor incididunt ut et dolore magna aliqua. Ut enim ad minim veniam</p>

  <div class="service" style="left:90px;top:204px">
    <div class="service__icon"><svg width="40" height="34" viewBox="0 0 40 34"><path d="M4 12h8l18-9v26L12 20H4z" fill="none" stroke="#f47b20" stroke-width="4" stroke-linejoin="round"/><path d="M8 20l3 11h5l-2-11" fill="#f47b20"/></svg></div>
    <div class="service__name">Network Administration</div>
    <div class="service__text">Lorem ipsum dolor sit amet,<br>consectetur adipisicing elit</div>
  </div>
  <div class="service" style="left:402px;top:204px">
    <div class="service__icon"><svg width="40" height="34" viewBox="0 0 40 34"><ellipse cx="15" cy="12" rx="14" ry="10" fill="#f47b20"/><path d="M6 19l-3 7 9-4z" fill="#f47b20"/><ellipse cx="27" cy="20" rx="12" ry="9" fill="#f47b20" stroke="#fff" stroke-width="2"/><path d="M33 26l4 6-9-4z" fill="#f47b20"/></svg></div>
    <div class="service__name">Desktop Support</div>
    <div class="service__text">Lorem ipsum dolor sit amet,<br>consectetur adipisicing elit</div>
  </div>
  <div class="service" style="left:714px;top:204px">
    <div class="service__icon"><svg width="42" height="32" viewBox="0 0 42 32"><path d="M10 30a9 9 0 0 1-1-18 11 11 0 0 1 21-3 9 9 0 0 1 4 21z" fill="#f47b20"/><path d="M18 11h6v8h5l-8 8-8-8h5z" fill="#fff"/></svg></div>
    <div class="service__name">Network Cabling</div>
    <div class="service__text">Lorem ipsum dolor sit amet,<br>consectetur adipisicing elit</div>
  </div>

  <div class="service" style="left:90px;top:324px">
    <div class="service__icon"><svg width="40" height="32" viewBox="0 0 40 32"><path d="M8 26C6 12 20 4 36 6 36 22 24 30 10 26z" fill="#f47b20"/><path d="M3 30C12 22 20 17 28 13" stroke="#fff" stroke-width="2.5" fill="none"/><path d="M3 30l4-4" stroke="#f47b20" stroke-width="3"/></svg></div>
    <div class="service__name">Wireless Networks</div>
    <div class="service__text">Lorem ipsum dolor sit amet,<br>consectetur adipisicing elit</div>
  </div>
  <div class="service" style="left:402px;top:324px">
    <div class="service__icon"><svg width="42" height="40" viewBox="0 0 42 40"><g fill="#f47b20"><circle cx="15" cy="22" r="9"/><rect x="12" y="9" width="6" height="26"/><rect x="2" y="19" width="26" height="6"/><rect x="12" y="9" width="6" height="26" transform="rotate(45 15 22)"/><rect x="12" y="9" width="6" height="26" transform="rotate(-45 15 22)"/><circle cx="32" cy="10" r="5"/><rect x="30" y="2" width="4" height="16"/><rect x="24" y="8" width="16" height="4"/><circle cx="32" cy="31" r="5"/><rect x="30" y="23" width="4" height="16"/><rect x="24" y="29" width="16" height="4"/></g><g fill="#fff"><circle cx="15" cy="22" r="3.5"/><circle cx="32" cy="10" r="2"/><circle cx="32" cy="31" r="2"/></g></svg></div>
    <div class="service__name">Antivirus Solutions</div>
    <div class="service__text">Lorem ipsum dolor sit amet,<br>consectetur adipisicing elit</div>
  </div>
  <div class="service" style="left:714px;top:324px">
    <div class="service__icon"><svg width="40" height="36" viewBox="0 0 40 36"><path d="M20 34 4 18A10 10 0 0 1 20 6a10 10 0 0 1 16 12z" fill="#f47b20"/></svg></div>
    <div class="service__name">Network Security</div>
    <div class="service__text">Lorem ipsum dolor sit amet,<br>consectetur adipisicing elit</div>
  </div>
</section>

<section class="works">
  <h2 class="section-title" style="top:50px">Recent Works</h2>
  <p class="section-lead" style="top:102px">Lorem ipsum dolor sit amet, consectetur adipisicing elit, sed do eiusmod tempor incididunt ut et dolore magna aliqua. Ut enim ad minim veniam</p>
</section>

</body>
</html>
```